Real Estate Webpage Design

We have an existing website: ferndaleestatecollective.com.au
We focus customised service mainly on Property Management and second-hand property sales.
We are not entirely happy about the current design and layout can stay roughly the same as the back end coding is linked to a CRM system.
We would like to see the design are more reachable to our clients and appearing.
Please check our Website Design Draft for more details.

Industry/Entity Type

Real estate Agency

Number of Pages Required

5+ page

Font styles to use
Sans Serif

Colors

Designer to choose colors to be used in the design.

```html
<!DOCTYPE html>
<html lang="en">
<head>
<meta charset="utf-8">
<title>Ferndale Estate Collective</title>
<link href="https://fonts.googleapis.com/css2?family=Cinzel:wght@400;500&family=Lato:ital,wght@0,400;0,700;1,400&display=swap" rel="stylesheet">
<style>
:root{
  --gold:#e9bd5c;
  --navy:#243247;
  --ink:#222;
  --text:#444;
  --grey-bg:#f5f5f5;
  --white:#fff;
}
*{margin:0;padding:0;box-sizing:border-box}
html,body{width:1200px;height:3892px;overflow:hidden}
body{position:relative;font-family:'Lato',sans-serif;color:var(--text);background:var(--white)}
.abs{position:absolute}
.serif{font-family:'Cinzel',serif}
.center{left:0;width:1200px;text-align:center}

/* hero */
.hero{top:0;left:0;width:1200px;height:680px;background:linear-gradient(180deg,#b9c3cc 0%,#c9c6bf 40%,#8a8a6a 75%,#6d7b42 100%)}
.hero-band{top:198px;left:0;width:1200px;height:331px;background:rgba(90,95,105,.55)}
.socials{top:18px;left:132px;display:flex;gap:15px}
.socials span{width:31px;height:31px;border:2px solid var(--navy);border-radius:50%;display:block}
.logo{top:22px;left:506px;display:flex;align-items:center;gap:10px}
.logo-mark{width:34px;height:34px;border:4px solid var(--gold)}
.logo-name{font-weight:700;font-size:30px;color:var(--gold);line-height:1}
.phone{top:11px;left:872px;width:194px;height:49px;border-radius:25px;background:var(--gold);display:flex;align-items:center;padding-left:12px;gap:14px;font-family:'Cinzel',serif;font-size:17px;color:var(--navy)}
.phone i{width:30px;height:30px;border-radius:50%;background:var(--navy);display:flex;align-items:center;justify-content:center}
.nav{top:92px;left:276px;display:flex;gap:37px;font-size:12px;font-weight:700;color:#111;text-transform:uppercase}
.nav .active{color:var(--gold)}
.hero-title{color:var(--white);font-family:'Cinzel',serif;line-height:1.1}
.hero-title .l1{font-size:56px}
.hero-title .l2{font-size:70px}

/* headings */
.ghost{font-family:'Cinzel',serif;color:rgba(0,0,0,.06);white-space:nowrap}
.h2{font-family:'Cinzel',serif;font-size:36px;color:#2a2a2a;letter-spacing:1px}
.rule{height:3px;background:var(--gold);left:538px;width:124px}

.about-text{left:160px;width:880px;text-align:center;font-size:13.5px;line-height:24px;color:#333}
.about-text p{margin-bottom:24px}

/* properties */
.listings{top:1114px;left:0;width:1200px;height:811px;background:var(--grey-bg)}
.tabs{top:1282px;left:0;width:1200px;display:flex;justify-content:center;gap:20px;font-size:13px;font-weight:700;color:#222}
.tabs .on{color:var(--gold);border-bottom:2px solid var(--gold);padding-bottom:10px}
.card{top:1345px;width:299px;height:461px;background:var(--white);padding:7px;text-align:center}
.card.raised{box-shadow:0 2px 10px rgba(0,0,0,.15)}
.card .photo{height:222px}
.card h3{font-family:'Cinzel',serif;font-weight:400;font-size:21px;color:#222;margin-top:18px}
.card .addr{font-size:13px;color:#333;margin-top:6px}
.feats{display:flex;justify-content:center;gap:22px;margin-top:14px}
.feat{width:62px;height:62px;border-radius:50%;background:var(--navy);color:var(--gold);display:flex;flex-direction:column;align-items:center;justify-content:center;font-size:13px;gap:2px}
.feat.gold{background:var(--gold);color:var(--navy)}
.price{font-family:'Cinzel',serif;font-size:30px;color:#222;margin-top:14px}

/* testimonial */
.testi{top:1925px;left:0;width:1200px;height:468px;background:linear-gradient(180deg,#3c4a5e,#2b384c 60%,#243146)}
.testi .ghost{color:rgba(255,255,255,.06)}
.quote{left:151px;width:898px;top:2135px;text-align:center;font-style:italic;font-size:13px;line-height:24px;color:#e8e8e8}
.qmark{font-family:'Cinzel',serif;font-size:42px;color:var(--gold);font-style:italic}
.dots{top:2280px;left:570px;display:flex;gap:4px}
.dots span{width:9px;height:9px;border-radius:50%;background:#fff}
.dots span:first-child{background:var(--gold)}

/* team */
.member{width:452px;height:314px}
.member .frame{position:absolute;inset:15px;border:2px solid rgba(255,255,255,.85)}
.member .name{position:absolute;left:108px;bottom:-17px;width:234px;height:47px;background:var(--white);display:flex;align-items:center;justify-content:center;font-family:'Cinzel',serif;font-size:18px;color:#222;box-shadow:0 1px 4px rgba(0,0,0,.08)}
.btn{top:3388px;left:502px;width:195px;height:50px;border-radius:25px;background:var(--gold);display:flex;align-items:center;justify-content:center;font-family:'Cinzel',serif;font-size:17px;color:var(--navy)}

/* footer */
.footer{top:3510px;left:0;width:1200px;height:382px;background:var(--navy);color:#fff}
.fcol h4{font-family:'Cinzel',serif;font-weight:400;font-size:18px;margin-bottom:14px}
.fcol li{list-style:none;font-size:13px;line-height:24px;display:flex;gap:10px}
.fcol li b{color:#fff;font-weight:700}
.divider{top:79px;width:1px;height:204px;background:rgba(255,255,255,.25)}
.fsocial{top:161px;left:940px;display:flex;gap:10px}
.fsocial span{width:34px;height:34px;border:2px solid #fff;border-radius:50%}
.fline{top:305px;left:50px;width:1100px;height:1px;background:rgba(255,255,255,.3)}
.copy{top:326px;left:0;width:1200px;text-align:center;font-size:13px}
</style>
</head>
<body>

<!-- hero -->
<div class="abs hero" role="img" aria-label="Photo of modern apartment buildings along a tree-lined path"></div>
<div class="abs hero-band"></div>
<div class="abs socials"><span></span><span></span><span></span><span></span></div>
<div class="abs logo"><span class="logo-mark"></span><span class="logo-name">Ferndale</span></div>
<div class="abs phone"><i><svg width="15" height="15" viewBox="0 0 24 24"><path fill="#e9bd5c" d="M6.6 10.8a15 15 0 0 0 6.6 6.6l2.2-2.2c.3-.3.7-.4 1-.2 1.1.4 2.3.6 3.6.6.6 0 1 .4 1 1V20c0 .6-.4 1-1 1A17 17 0 0 1 3 4c0-.6.4-1 1-1h3.5c.6 0 1 .4 1 1 0 1.3.2 2.5.6 3.6.1.3 0 .7-.2 1z"/></svg></i>02 5550 1234</div>
<nav class="abs nav"><span class="active">Home</span><span>About Us</span><span>Leasing</span><span>Buy</span><span>Sell</span><span>Our Team</span><span>Blog</span><span>Contact Us</span></nav>
<div class="abs center hero-title" style="top:255px"><div class="l1">WELCOME TO</div><div class="l2">FERNDALE ESTATE COLLECTIVE</div></div>
<svg class="abs" style="top:430px;left:583px" width="34" height="34" viewBox="0 0 34 34"><circle cx="17" cy="17" r="17" fill="#fff"/><path d="M13 10l11 7-11 7z" fill="#555"/></svg>
<svg class="abs" style="top:615px;left:588px" width="24" height="52" viewBox="0 0 24 52"><path d="M12 0v48M2 38l10 12 10-12" stroke="#fff" stroke-width="3" fill="none"/></svg>

<!-- about -->
<div class="abs center ghost" style="top:730px;font-size:76px">ABOUT</div>
<div class="abs center h2" style="top:772px">FERNDALE – A PLACE TO CALL HOME</div>
<div class="abs rule" style="top:830px"></div>
<div class="abs about-text" style="top:852px">
  <p>Ferndale is a place to call home. Buying a property is one of the most expensive expenses and important assets for people. Ferndale is a real estate company located in Gungahlin, Canberra.</p>
  <p>Being a portfolio sales agent and property manager, coupled with our high-profile international real estate experience, Ferndale is considered a market leader on the cutting edge with deep industry knowledge, ranging from landlord-tenant relationships, residential purchases.</p>
  <p>Being a portfolio sales agent and property manager, coupled with our high-profile international real estate experience, Ferndale is considered a market leader on the cutting edge with deep industry knowledge, ranging from landlord-tenant relationships, residential purchases.</p>
</div>

<!-- listings -->
<div class="abs listings"></div>
<div class="abs center ghost" style="top:1148px;font-size:72px">PROPERTY GROUP</div>
<div class="abs center h2" style="top:1189px">THIS MONTH AT FERNDALE ESTATE COLLECTIVE</div>
<div class="abs rule" style="top:1252px"></div>
<div class="abs tabs"><span>FOR SALE</span><span>|</span><span class="on">FOR LEASE</span><span>|</span><span>OPEN TIMES</span><span>|</span><span>SOLD</span><span>|</span><span>LEASED</span></div>

<svg width="0" height="0" style="position:absolute">
  <symbol id="i-bed" viewBox="0 0 16 12"><path d="M1 2v9M1 8h14v3M4 5h10v3" stroke="currentColor" stroke-width="2" fill="none"/></symbol>
  <symbol id="i-bath" viewBox="0 0 16 12"><path d="M2 6h12v2a3 3 0 0 1-3 3H5a3 3 0 0 1-3-3zM4 6V2h3" stroke="currentColor" stroke-width="2" fill="none"/></symbol>
  <symbol id="i-car" viewBox="0 0 16 12"><path d="M2 7l2-5h8l2 5v4H2z" fill="currentColor"/></symbol>
</svg>

<div class="abs card" style="left:127px">
  <div class="photo" role="img" aria-label="Photo of a two-storey house with double garage" style="background:linear-gradient(180deg,#6d95c9,#d8d6d0 45%,#8a7c70)"></div>
  <h3>RED HILL</h3><div class="addr">14 Marlow Street Red Hill</div>
  <div class="feats"><div class="feat"><svg width="16" height="12"><use href="#i-bed"/></svg>4</div><div class="feat gold"><svg width="16" height="12"><use href="#i-bath"/></svg>2</div><div class="feat"><svg width="16" height="12"><use href="#i-car"/></svg>2</div></div>
  <div class="price">$1400 PW</div>
</div>
<div class="abs card raised" style="left:450px">
  <div class="photo" role="img" aria-label="Photo of a furnished apartment living room" style="background:linear-gradient(180deg,#d9d9d5,#a99c8c 60%,#7a5a3e)"></div>
  <h3>BRADDON</h3><div class="addr">12/6 Keller Street Braddon</div>
  <div class="feats"><div class="feat"><svg width="16" height="12"><use href="#i-bed"/></svg>1</div><div class="feat gold"><svg width="16" height="12"><use href="#i-bath"/></svg>1</div><div class="feat"><svg width="16" height="12"><use href="#i-car"/></svg>1</div></div>
  <div class="price">$560 PW</div>
</div>
<div class="abs card" style="left:774px">
  <div class="photo" role="img" aria-label="Photo of a single-storey brick home with garden" style="background:linear-gradient(180deg,#2f6fc4,#7aa2d6 45%,#8a7a62 75%,#a08a6c)"></div>
  <h3>GRIFFITH</h3><div class="addr">3 Linden Street Griffith</div>
  <div class="feats"><div class="feat"><svg width="16" height="12"><use href="#i-bed"/></svg>4</div><div class="feat gold"><svg width="16" height="12"><use href="#i-bath"/></svg>2</div><div class="feat"><svg width="16" height="12"><use href="#i-car"/></svg>3</div></div>
  <div class="price">$1300 PW</div>
</div>

<!-- testimonials -->
<div class="abs testi" role="img" aria-label="Dimmed photo of a modern house at dusk"></div>
<div class="abs center ghost" style="top:1985px;font-size:76px;color:rgba(255,255,255,.06)">TESTIMONIALS</div>
<div class="abs center h2" style="top:2030px;color:#fff">WHAT OUR CLIENTS SAY</div>
<div class="abs rule" style="top:2090px"></div>
<div class="abs qmark" style="top:2085px;left:155px">“</div>
<div class="abs quote">perspiciatis unde omnis iste natus error sit voluptatem accusantium doloremque laudantium, totam rem aperiam, eaque ipsa quae ab illo inventore veritatis et quasi architecto beatae vitae dicta sunt explicabo. Nemo enim ipsam voluptatem quia voluptas sit aspernatur aut odit aut fugit, sed quia consequuntur magni dolores eos qui ratione voluptatem sequi nesciunt. Neque porro quisquam est, qui dolorem ipsum quia dolor sit amet, consectetur, adipisci velit, sed quia non numquam eius modi tempora incidunt ut labore et dolore magnam aliquam quaerat voluptatem. Ut enim ad minima veniam, quis nostrum exercitationem ullam corporis suscipit laboriosam, nisi ut aliquid ex ea commodi consequatur.</div>
<div class="abs qmark" style="top:2225px;left:770px">”</div>
<div class="abs dots"><span></span><span></span><span></span><span></span><span></span></div>

<!-- team -->
<div class="abs center ghost" style="top:2470px;font-size:86px">MEET OUR TEAM</div>
<div class="abs center h2" style="top:2515px">MEET OUR TEAM</div>
<div class="abs rule" style="top:2575px"></div>

<div class="abs member" style="top:2617px;left:133px" role="img" aria-label="Portrait photo of team member Wei Chen"><div style="position:absolute;inset:0;background:linear-gradient(180deg,#9a9a9a,#6e6e6e 60%,#2c2c30)"></div><div class="frame"></div><div class="name">WEI CHEN</div></div>
<div class="abs member" style="top:2617px;left:615px" role="img" aria-label="Portrait photo of team member Mara Lin"><div style="position:absolute;inset:0;background:linear-gradient(180deg,#8a8d96,#6b6e78 60%,#2a2b30)"></div><div class="frame"></div><div class="name">MARA LIN</div></div>
<div class="abs member" style="top:2992px;left:133px" role="img" aria-label="Portrait photo of team member Tessa Hu"><div style="position:absolute;inset:0;background:linear-gradient(180deg,#505050,#3a3a3a 60%,#1e1e1e)"></div><div class="frame"></div><div class="name">TESSA HU</div></div>
<div class="abs member" style="top:2992px;left:615px" role="img" aria-label="Photo of team member Owen Park in front of the office shopfront"><div style="position:absolute;inset:0;background:linear-gradient(90deg,#f2d400,#9fb3c6 30%,#9fb3c6 70%,#f2d400)"></div><div class="frame"></div><div class="name">OWEN PARK</div></div>

<div class="abs btn">VIEW ALL</div>

<!-- footer -->
<footer class="abs footer">
  <div class="abs fcol" style="top:76px;left:95px">
    <h4>CONTACT US</h4>
    <ul>
      <li><svg width="10" height="24" viewBox="0 0 10 14"><path d="M5 0a5 5 0 0 0-5 5c0 4 5 9 5 9s5-5 5-9a5 5 0 0 0-5-5zm0 7a2 2 0 1 1 0-4 2 2 0 0 1 0 4z" fill="#fff"/></svg><span>18/7 Wattle Grove Ave, Gungahlin,<br>ACT, 2990</span></li>
      <li style="margin-top:16px"><svg width="10" height="24" viewBox="0 0 24 24"><path fill="#fff" d="M6.6 10.8a15 15 0 0 0 6.6 6.6l2.2-2.2c.3-.3.7-.4 1-.2 1.1.4 2.3.6 3.6.6.6 0 1 .4 1 1V20c0 .6-.4 1-1 1A17 17 0 0 1 3 4c0-.6.4-1 1-1h3.5c.6 0 1 .4 1 1 0 1.3.2 2.5.6 3.6.1.3 0 .7-.2 1z"/></svg>02 5550 1234</li>
      <li style="margin-top:10px"><svg width="10" height="24" viewBox="0 0 10 10"><rect x="0" y="3" width="10" height="7" fill="#fff"/><rect x="2" y="0" width="6" height="3" fill="#fff"/></svg>02 5550 5678</li>
      <li style="margin-top:16px"><svg width="11" height="24" viewBox="0 0 12 9"><rect width="12" height="9" fill="#fff"/><path d="M0 0l6 5 6-5" stroke="#243247" fill="none"/></svg>hello@ferndaleestate.example</li>
    </ul>
  </div>
  <div class="abs divider" style="left:370px"></div>
  <div class="abs fcol" style="top:76px;left:423px">
    <h4>QUICK LINKS</h4>
    <ul><li><b>»</b>Home</li><li><b>»</b>About Us</li><li><b>»</b>Leasing</li><li><b>»</b>Buy</li><li><b>»</b>Sell</li><li><b>»</b>Our Team</li><li><b>»</b>Blog</li><li><b>»</b>Contact Us</li></ul>
  </div>
  <div class="abs divider" style="left:618px"></div>
  <div class="abs fcol" style="top:76px;left:683px">
    <h4>LEGAL</h4>
    <ul><li><b>»</b>Privacy</li><li><b>»</b>Complaint Handling</li><li><b>»</b>Dispute Resolution</li><li><b>»</b>Due Diligence Checklist</li><li><b>»</b>Sitemap</li></ul>
  </div>
  <div class="abs divider" style="left:881px"></div>
  <div class="abs fsocial"><span></span><span></span><span></span><span></span></div>
  <div class="abs fline"></div>
  <div class="abs copy">© copyrights 2022 Ferndale Estate Collective &nbsp;|&nbsp;&nbsp;&nbsp; All rights reserved.</div>
</footer>

</body>
</html>
```